Website design with eCommerce for revolutionary new product in the manufacturing industry.

We need a website designed for a precision manufacturing company based in the suburbs of Minneapolis, Minnesota called Velkrin Manufacturing. We have a revolutionary new product, the TARN LOCK, to introduce and sell through an eCommerce storefront. The website would include company information, product information, and the storefront. Green is a color that represents Velkrin Manufacturing. The final design should communicate that we exclusively offer premium products at a premium price. The design should also let the customer know they are the focus of our work.

Target Market(s)

Machinists and machine shops

Industry/Entity Type

Manufacturing and machine shops

Coding

Coded - Design and coding required

Font styles to use
Sans Serif

Colors
59FF00
82FF00
B8FF75
E3FFCB
F4FFEA

Requirements
Must have
• eCommerce storefront, Made in USA references
Nice to have
• Home page, TARN LOCK Product page, About Us, Capabilities, Contact, etc.
Should not have
• Should not be too much text and reading.

```html
<!DOCTYPE html>
<html lang="en">
<head>
<meta charset="utf-8">
<title>Velkrin Manufacturing</title>
<link href="https://fonts.googleapis.com/css2?family=Poppins:wght@400;500;600;700;800&display=swap" rel="stylesheet">
<style>
:root{
  --green:#59FF00;
  --green-2:#82FF00;
  --green-soft:#B8FF75;
  --green-pale:#E3FFCB;
  --green-mist:#F4FFEA;
  --ink:#141414;
  --text:#555;
  --muted:#8a8a8a;
  --line:#d9d9d9;
  --panel:#efefef;
  --black:#0b0b0b;
}
*{box-sizing:border-box;margin:0;padding:0}
html,body{width:1200px;height:3856px;overflow:hidden}
body{font-family:'Poppins',sans-serif;color:var(--ink);background:#fff;position:relative}
.abs{position:absolute}
.brand{font-weight:800;font-size:30px;color:var(--ink);letter-spacing:-0.5px;display:flex;align-items:center;gap:10px}
.brand .dot{width:14px;height:14px;background:var(--green);border-radius:50%}

/* header */
.site-header{left:0;top:0;width:1200px;height:70px;background:#fff;border-bottom:1px solid #eee}
.site-header .brand{position:absolute;left:60px;top:16px}
.topbar{position:absolute;right:48px;top:6px;display:flex;align-items:center;gap:26px;font-size:12px;color:var(--text)}
.topbar span{display:flex;align-items:center;gap:6px}
.ico-round{width:18px;height:18px;border-radius:50%;background:var(--ink);display:inline-block}
.social{display:flex;gap:8px}
.social i{width:20px;height:20px;border-radius:50%;background:var(--ink);display:block}
.main-nav{position:absolute;left:370px;top:38px;display:flex;gap:26px;font-size:13px;font-weight:500;align-items:center}
.search{position:absolute;left:880px;top:36px;width:170px;height:24px;border:1px solid var(--line);border-radius:3px;font-size:11px;color:var(--muted);padding:4px 10px}
.user{position:absolute;left:1070px;top:36px}

/* hero */
.hero{left:0;top:70px;width:1200px;height:630px;background:radial-gradient(circle at 70% 40%,#5a6a78 0%,#2a3440 45%,#121820 100%)}
.hero h1{position:absolute;left:40px;top:408px;color:#fff;font-size:36px;font-weight:800;letter-spacing:.5px}
.hero p{position:absolute;left:40px;top:460px;color:#fff;font-size:15px;width:360px;line-height:1.5}
.btn-ghost{position:absolute;left:40px;top:530px;padding:8px 20px;border:1.5px solid #fff;border-radius:3px;color:#fff;font-size:11px;font-weight:700}
.dots{position:absolute;left:548px;top:570px;display:flex;gap:10px}
.dots i{width:12px;height:12px;border-radius:50%;border:2px solid #fff;display:block}
.dots i:first-child{background:#fff}

/* banners */
.tag{position:absolute;height:48px}
.tag span{position:absolute;left:0;top:0;width:100%;height:100%;display:flex;align-items:center;padding-left:40px;font-weight:800;font-size:22px;color:var(--ink)}

/* what we do */
.about-photo{left:120px;top:800px;width:380px;height:380px;border-radius:12px;background:linear-gradient(135deg,#6b6b6b,#2c2c2c 60%,#4a4a4a);box-shadow:0 10px 30px rgba(0,0,0,.2)}
.about-copy{left:620px;top:896px;width:470px;font-size:13.5px;color:var(--text);line-height:1.75}
.about-copy p+p{margin-top:14px}
.btn-line{position:absolute;padding:8px 22px;border:2px solid var(--green);border-radius:20px;font-size:11px;font-weight:700;color:var(--ink)}

/* products */
.products{left:0;top:1280px;width:1200px;height:660px;background:var(--panel)}
.arrow-title{position:absolute;left:420px;top:60px}
.arrow-title span{position:absolute;left:0;top:0;width:300px;height:80px;display:flex;align-items:center;justify-content:center;font-weight:800;font-size:22px}
.card{position:absolute;top:170px;width:270px;height:420px;background:#fff;box-shadow:0 2px 10px rgba(0,0,0,.08)}
.card .shot{height:240px;background:linear-gradient(160deg,#2b2b2b,#111 70%);position:relative}
.card .shot::after{content:"";position:absolute;left:70px;top:60px;width:110px;height:110px;background:linear-gradient(135deg,var(--green-2),#3fb800);border-radius:6px;opacity:.85}
.card .meta{text-align:center;padding-top:18px}
.stars{color:#f5b400;font-size:14px;letter-spacing:2px}
.stars em{color:var(--muted);font-style:normal;font-size:11px;letter-spacing:0}
.card h3{font-size:19px;font-weight:700;margin-top:6px}
.price{font-size:13px;margin-top:4px}
.price s{color:var(--muted);margin-left:6px}
.btn-shop{display:inline-block;margin-top:12px;background:var(--green);padding:7px 26px;border-radius:3px;font-size:11px;font-weight:700}

/* capabilities */
.cap-list{left:100px;top:2140px;width:380px}
.cap{display:flex;gap:18px;margin-bottom:26px}
.cap h4{font-size:15px;font-weight:700}
.cap p{font-size:12px;color:var(--text);line-height:1.6;margin-top:2px}
.cap svg{flex:none}
.cap-photo{left:670px;top:2040px;width:460px;height:460px;border-radius:50%;background:radial-gradient(circle,#8d8d8d,#3d3d3d 60%,#1c1c1c)}

/* why */
.why-photo{left:0;top:2700px;width:600px;height:340px;background:linear-gradient(135deg,#9a9a9a,#555 55%,#2b2b2b)}
.why-panel{left:600px;top:2700px;width:600px;height:340px;background:var(--green-soft)}
.why-panel p{position:absolute;left:90px;top:98px;width:440px;font-size:13px;line-height:1.6;color:var(--ink)}
.why-list{position:absolute;left:90px;top:180px;list-style:none;font-size:13px}
.why-list li{display:flex;align-items:center;gap:16px;height:32px}

/* contact */
.info{left:120px;top:3190px;width:300px}
.info .row{display:flex;gap:16px;margin-bottom:24px}
.info .pin{width:34px;height:34px;border-radius:50%;background:var(--green);flex:none;display:flex;align-items:center;justify-content:center}
.info h5{font-size:13px;font-weight:700}
.info p{font-size:12px;color:var(--text);line-height:1.5}
.field{position:absolute;width:200px;height:40px;border:1px solid var(--line);border-radius:3px;font-size:12px;color:var(--muted);padding:11px 12px}
.message{left:700px;top:3180px;width:380px;height:150px;border:1px solid var(--line);border-radius:3px;font-size:12px;color:var(--muted);padding:11px 12px}
.btn-submit{left:700px;top:3340px;width:380px;height:40px;background:var(--green);border-radius:3px;font-size:12px;font-weight:700;display:flex;align-items:center;justify-content:center}

/* footer */
.site-footer{left:0;top:3480px;width:1200px;height:376px;background:var(--black);color:#fff}
.site-footer .brand{position:absolute;left:60px;top:50px;color:#fff}
.site-footer .blurb{position:absolute;left:60px;top:120px;width:300px;font-size:12px;line-height:1.6;color:#ddd}
.fcol{position:absolute;top:50px}
.fcol h6{font-size:15px;font-weight:700;margin-bottom:16px}
.fcol a{display:block;font-size:12px;color:#ddd;margin-bottom:8px;text-decoration:none}
.fsocial{display:flex;gap:12px}
.fsocial i{width:28px;height:28px;border-radius:50%;background:#fff;display:block}
.copy{position:absolute;left:0;top:340px;width:1200px;text-align:center;font-size:11px;color:#ccc;border-top:1px solid #333;padding-top:10px}
.copy b{position:absolute;right:40px;font-weight:400}
</style>
</head>
<body>

<header class="abs site-header">
  <div class="brand">Velkrin <span class="dot"></span></div>
  <div class="topbar">
    <span><i class="ico-round"></i>info@velkrinmfg.com</span>
    <span><i class="ico-round"></i>+1 (612) 555 0148</span>
    <div class="social"><i></i><i></i><i></i><i></i></div>
  </div>
  <nav class="main-nav"><span>Home</span><span>TARN LOCK Product</span><span>About</span><span>Capabilities</span><span>Contact</span></nav>
  <div class="search">Search</div>
  <svg class="user" width="20" height="22" viewBox="0 0 20 22"><circle cx="10" cy="6" r="5" fill="none" stroke="#141414" stroke-width="2"/><path d="M1 21c0-5 4-8 9-8s9 3 9 8" fill="none" stroke="#141414" stroke-width="2"/></svg>
</header>

<section class="abs hero" role="img" aria-label="Machined brass and steel parts arranged on a shop table">
  <h1>VELKRIN MANUFACTURING</h1>
  <p>The machining bug when he took a high school machine shop class, and has been ever growing his abilities!</p>
  <span class="btn-ghost">WATCH VIDEO</span>
  <div class="dots"><i></i><i></i><i></i><i></i></div>
</section>

<div class="abs about-photo" role="img" aria-label="Close-up of precision machined metal grid"></div>
<svg class="tag" style="left:560px;top:810px;width:300px" viewBox="0 0 300 48"><polygon points="0,0 260,0 300,24 260,48 0,48 20,24" fill="#59FF00"/></svg>
<div class="tag" style="left:590px;top:810px;width:300px"><span>WHAT WE DO</span></div>
<div class="abs about-copy">
  <p>We are a machine shop with complete end-to-end manufacturing capabilities. We can take an idea or need, and bring it to a complete physical product. We can design and build your part.</p>
  <p>We love working directly with customers to manufacture their products, and help make it better where appropriate. We can work with as little as a verbal description, up to following fully defined customer specifications.</p>
</div>
<span class="btn-line" style="left:620px;top:1120px">LEARN MORE</span>

<section class="abs products">
  <svg class="arrow-title" width="360" height="80" viewBox="0 0 360 80"><polygon points="2,10 300,10 300,2 356,40 300,78 300,70 2,70 30,40" fill="none" stroke="#141414" stroke-width="2"/></svg>
  <div class="arrow-title"><span style="left:20px">OUR PRODUCT</span></div>

  <article class="card" style="left:30px"><div class="shot" role="img" aria-label="Green TARN LOCK clamp in foam case"></div><div class="meta"><div class="stars">★★★★★ <em>(45)</em></div><h3>TL-001A</h3><div class="price">$55.5 <s>$66.0</s></div><span class="btn-shop">SHOP NOW</span></div></article>
  <article class="card" style="left:320px"><div class="shot" role="img" aria-label="Green TARN LOCK clamp in foam case"></div><div class="meta"><div class="stars">★★★★★ <em>(45)</em></div><h3>TL-002A</h3><div class="price">$45.5 <s>$56.0</s></div><span class="btn-shop">SHOP NOW</span></div></article>
  <article class="card" style="left:610px"><div class="shot" role="img" aria-label="Green TARN LOCK clamp in foam case"></div><div class="meta"><div class="stars">★★★★★ <em>(45)</em></div><h3>TL-003A</h3><div class="price">$60.5 <s>$70.0</s></div><span class="btn-shop">SHOP NOW</span></div></article>
  <article class="card" style="left:900px"><div class="shot" role="img" aria-label="Green TARN LOCK clamp in foam case"></div><div class="meta"><div class="stars">★★★★★ <em>(45)</em></div><h3>TL-004A</h3><div class="price">$58.5 <s>$68.0</s></div><span class="btn-shop">SHOP NOW</span></div></article>
</section>

<svg class="tag" style="left:100px;top:2050px;width:300px" viewBox="0 0 300 48"><polygon points="0,0 260,0 300,24 260,48 0,48 20,24" fill="#59FF00"/></svg>
<div class="tag" style="left:130px;top:2050px;width:300px"><span>CAPABILITIES</span></div>
<div class="abs cap-list">
  <div class="cap"><svg width="34" height="34" viewBox="0 0 34 34"><path d="M4 30L30 4M8 4l22 22M4 26l4 4" stroke="#141414" stroke-width="2.5" fill="none"/></svg><div><h4>CAD Design</h4><p>Do you have something that needs to be created but no method of capturing the design?</p></div></div>
  <div class="cap"><svg width="34" height="34" viewBox="0 0 34 34"><rect x="5" y="12" width="24" height="14" rx="2" fill="none" stroke="#141414" stroke-width="2.5"/><rect x="10" y="4" width="14" height="8" fill="none" stroke="#141414" stroke-width="2.5"/><rect x="10" y="22" width="14" height="9" fill="#fff" stroke="#141414" stroke-width="2.5"/></svg><div><h4>FFF 3D Printing</h4><p>Using Fused Filament Fabrication we can 3D print prototypes for evaluation, or fully.</p></div></div>
  <div class="cap"><svg width="34" height="34" viewBox="0 0 34 34"><circle cx="12" cy="12" r="7" fill="none" stroke="#141414" stroke-width="2.5"/><rect x="16" y="16" width="14" height="14" fill="none" stroke="#141414" stroke-width="2.5"/></svg><div><h4>Prototypes</h4><p>We can make custom, one-off parts such as racing components, or make the first sample.</p></div></div>
</div>
<span class="btn-line" style="left:100px;top:2440px">LEARN MORE</span>
<div class="abs cap-photo" role="img" aria-label="Machined metal pattern viewed from above"></div>

<div class="abs why-photo" role="img" aria-label="Rows of machined metal fittings"></div>
<section class="abs why-panel">
  <svg class="tag" style="left:-40px;top:36px;width:420px" viewBox="0 0 420 48"><polygon points="0,0 380,0 420,24 380,48 0,48 20,24" fill="#82FF00"/></svg>
  <div class="tag" style="left:0;top:36px;width:420px"><span style="font-size:19px">WHY VELKRIN MANUFACTURING?</span></div>
  <p>Because there is a better way, and we will find it, even if it's the hard way. We believe in working harder and smarter to achieve.</p>
  <ul class="why-list">
    <li><svg width="28" height="10" viewBox="0 0 28 10"><path d="M0 5h26M21 1l5 4-5 4" stroke="#141414" stroke-width="2" fill="none"/></svg>Our success is measured in your success</li>
    <li><svg width="28" height="10" viewBox="0 0 28 10"><path d="M0 5h26M21 1l5 4-5 4" stroke="#141414" stroke-width="2" fill="none"/></svg>Focused on your needs and making excellent parts</li>
    <li><svg width="28" height="10" viewBox="0 0 28 10"><path d="M0 5h26M21 1l5 4-5 4" stroke="#141414" stroke-width="2" fill="none"/></svg>Exceeding your expectations</li>
  </ul>
</section>

<svg class="tag" style="left:430px;top:3070px;width:340px" viewBox="0 0 340 48"><polygon points="0,0 300,0 340,24 300,48 0,48 20,24" fill="#59FF00"/></svg>
<div class="tag" style="left:475px;top:3070px;width:300px"><span>CONTACT US</span></div>
<div class="abs info">
  <div class="row"><span class="pin"><svg width="14" height="18" viewBox="0 0 14 18"><path d="M7 17S1 10 1 6.5a6 6 0 0112 0C13 10 7 17 7 17z" fill="#141414"/></svg></span><div><h5>LOCATION</h5><p>Plymouth, Minnesota, USA<br>Built and shipped locally</p></div></div>
  <div class="row"><span class="pin"><svg width="16" height="16" viewBox="0 0 16 16"><path d="M3 1l3 3-2 2c1 2 3 4 6 6l2-2 3 3-2 2C7 15 1 9 1 3z" fill="#141414"/></svg></span><div><h5>CALL US</h5><p>+1 (612) 555 0148</p></div></div>
  <div class="row"><span class="pin"><svg width="16" height="12" viewBox="0 0 16 12"><rect x="1" y="1" width="14" height="10" fill="none" stroke="#141414" stroke-width="2"/><path d="M1 1l7 6 7-6" fill="none" stroke="#141414" stroke-width="2"/></svg></span><div><h5>EMAIL US</h5><p>hello@velkrinmfg.com</p></div></div>
</div>
<div class="field" style="left:480px;top:3180px">First Name</div>
<div class="field" style="left:480px;top:3230px">Last Name</div>
<div class="field" style="left:480px;top:3280px">Phone No</div>
<div class="field" style="left:480px;top:3340px">Email Address</div>
<div class="abs message">Type Your Message</div>
<div class="abs btn-submit">SUBMIT NOW</div>

<footer class="abs site-footer">
  <div class="brand">Velkrin <span class="dot"></span></div>
  <p class="blurb">Precision parts made in the USA for machinists and machine shops who expect premium tools, careful work and honest service from the first cut.</p>
  <div class="fcol" style="left:440px"><h6>QUICK LINKS</h6><a>Home</a><a>Product</a><a>About</a><a>Capabilities</a><a>Contact</a></div>
  <div class="fcol" style="left:670px"><h6>CAPABILITIES</h6><a>CAD Design</a><a>FFF 3D Printing</a><a>Prototypes</a><a>Vertical CNC Machining</a><a>Laser Marking</a></div>
  <div class="fcol" style="left:930px"><h6>FOLLOW US</h6><div class="fsocial"><i></i><i></i><i></i><i></i></div></div>
  <div class="copy">Copyrights ©2022 Velkrin MFG All Rights Reserved.<b>USA</b></div>
</footer>

</body>
</html>
```